Redesign of business card for Cedar Ridge Mechanical

We are looking for a new design for our business cards for Cedar Ridge Mechanical. We are a plumbing & HVAC construction company, operating on the West Coast of Canada and USA. Logo attached.
Industry/Entity Type
Construction - Plumbing & HVAC
Contact Information for Business Card
Name, address, phone numbers, email, website address
Look and feel
Each slider illustrates characteristics of the customer's brand and the style your logo design should communicate.

```html
<!DOCTYPE html>
<html lang="en">
<head>
<meta charset="UTF-8">
<title>Cedar Ridge Mechanical — Business Card</title>
<link href="https://fonts.googleapis.com/css2?family=Poppins:wght@300;400;600;700&display=swap" rel="stylesheet">
<style>
  :root {
    --stage: #222223;
    --card-dark: #1f1f22;
    --card-dark-tone: #2b2b2e;
    --card-light: #e4e5e5;
    --ink-light: #ffffff;
    --ink-soft: #d9d9db;
    --ink-emboss: #cfd0d0;
  }
  * { margin: 0; padding: 0; box-sizing: border-box; }
  html, body {
    width: 1200px; height: 780px; overflow: hidden;
    background: var(--stage);
    font-family: "Poppins", sans-serif;
  }
  .canvas {
    width: 1200px; height: 780px;
    display: flex; align-items: center; justify-content: center; gap: 40px;
  }
  .card {
    width: 540px; height: 309px;
    position: relative; overflow: hidden;
    box-shadow: 0 18px 40px rgba(0,0,0,.45);
  }
  /* Front */
  .card--front { background: var(--card-dark); color: var(--ink-light); }
  .front__tone {
    position: absolute; right: -60px; top: -40px;
    width: 300px; height: 300px;
    background: var(--card-dark-tone);
    opacity: .55;
  }
  .front__content { position: absolute; left: 40px; top: 40px; }
  .brand { display: flex; align-items: center; gap: 10px; }
  .brand__square { width: 22px; height: 22px; background: var(--ink-light); }
  .brand__name { font-weight: 600; font-size: 17px; letter-spacing: .5px; text-transform: uppercase; }
  .person { display: flex; gap: 10px; margin-top: 26px; }
  .person__bar { width: 8px; background: var(--ink-light); }
  .person__name { font-size: 24px; line-height: 1.1; font-weight: 300; }
  .person__name strong { font-weight: 700; }
  .person__role { font-size: 13px; font-weight: 300; color: var(--ink-soft); }
  .address { margin-top: 20px; font-size: 12.5px; font-weight: 300; line-height: 1.45; color: var(--ink-soft); }
  .contacts { list-style: none; margin-top: 12px; font-size: 12.5px; font-weight: 300; line-height: 1.55; color: var(--ink-soft); }
  .contacts li { display: flex; align-items: center; gap: 8px; }
  .contacts svg { width: 12px; height: 12px; fill: var(--ink-light); }
  /* Back */
  .card--back {
    background: var(--card-light);
    display: flex; align-items: center; justify-content: center; gap: 14px;
  }
  .back__square { width: 34px; height: 34px; background: var(--ink-emboss); }
  .back__name {
    font-weight: 600; font-size: 26px; letter-spacing: 1px;
    text-transform: uppercase; color: var(--ink-emboss);
  }
</style>
</head>
<body>
<main class="canvas">
  <section class="card card--front">
    <div class="front__tone"></div>
    <div class="front__content">
      <div class="brand">
        <span class="brand__square"></span>
        <span class="brand__name">Cedar Ridge Mechanical</span>
      </div>
      <div class="person">
        <span class="person__bar"></span>
        <div>
          <p class="person__name"><strong>Marta</strong> Kovalenko</p>
          <p class="person__role">Founder &amp; CEO</p>
        </div>
      </div>
      <p class="address">1840 Harbor Ln. Suite 310<br>Tacoma, WA 98402</p>
      <ul class="contacts">
        <li><svg viewBox="0 0 24 24"><path d="M6.6 10.8a15 15 0 0 0 6.6 6.6l2.2-2.2a1 1 0 0 1 1-.25 11.4 11.4 0 0 0 3.6.57 1 1 0 0 1 1 1V20a1 1 0 0 1-1 1A17 17 0 0 1 3 4a1 1 0 0 1 1-1h3.5a1 1 0 0 1 1 1c0 1.25.2 2.45.57 3.57a1 1 0 0 1-.25 1z"/></svg>(253) 555-0147</li>
        <li><svg viewBox="0 0 24 24"><circle cx="12" cy="12" r="10"/></svg>info@yourwebsite.com</li>
        <li><svg viewBox="0 0 24 24"><path d="M2 5h20v14H2z M2 5l10 8 10-8" /></svg>www.yourwebsite.com</li>
      </ul>
    </div>
  </section>
  <section class="card card--back">
    <span class="back__square"></span>
    <span class="back__name">Cedar Ridge Mechanical</span>
  </section>
</main>
</body>
</html>
```